Automotive Accessories Business Card

Design a business template that match our new logo design and our industry.

https://www.qelmotorgear.com/

Target Market(s)

Aftermarket auto parts and accessories

Industry/Entity Type

automotive

Contact Information for Business Card

company logo

Font styles to use
Serif
Sans Serif

Colors
EB3D1F
EC4F4E
F09395
F8D3D4
FCEDEE

```html
<!DOCTYPE html>
<html lang="en">
<head>
<meta charset="utf-8">
<title>QEL Motor Gear – Business Card</title>
<link rel="stylesheet" href="https://fonts.googleapis.com/css2?family=Montserrat:wght@400;500;700&display=swap">
<style>
  :root {
    --stage: #d9d9d9;
    --card: #414042;
    --card-deep: #353437;
    --accent: #e11d26;
    --text-light: #ffffff;
    --text-muted: #e6e6e6;
  }
  html, body {
    margin: 0;
    width: 1200px;
    height: 900px;
    overflow: hidden;
    background: var(--stage);
    font-family: "Montserrat", sans-serif;
  }
  .stage {
    position: relative;
    width: 1200px;
    height: 900px;
  }
  .card {
    position: absolute;
    left: 250px;
    width: 700px;
    height: 400px;
    background: var(--card);
    border-bottom: 7px solid var(--accent);
    box-shadow: 0 10px 24px rgba(0,0,0,0.25);
    box-sizing: border-box;
  }
  .card--front { top: 34px; }
  .card--back { top: 466px; }

  .front-wordmark {
    position: absolute;
    left: 0; right: 0; top: 50%;
    transform: translateY(-50%);
    text-align: center;
    font-weight: 700;
    font-size: 40px;
    letter-spacing: 3px;
    color: var(--card-deep);
  }

  .brand {
    position: absolute;
    left: 64px;
    top: 128px;
    display: flex;
    align-items: center;
    gap: 12px;
  }
  .brand-mark {
    width: 22px;
    height: 22px;
    background: var(--accent);
  }
  .brand-name {
    font-weight: 700;
    font-size: 26px;
    letter-spacing: 1.5px;
    color: var(--text-light);
  }

  .person {
    position: absolute;
    right: 0;
    top: 50px;
    display: flex;
    align-items: stretch;
  }
  .person-text {
    text-align: right;
    padding-right: 14px;
  }
  .person-name {
    font-weight: 700;
    font-size: 24px;
    letter-spacing: 1px;
    color: var(--accent);
    line-height: 1.1;
  }
  .person-role {
    font-size: 15px;
    color: var(--text-muted);
    margin-top: 4px;
  }
  .person-bar {
    width: 20px;
    background: var(--accent);
  }

  .contact {
    position: absolute;
    left: 64px;
    bottom: 40px;
    color: var(--text-light);
    font-size: 16px;
    line-height: 1.45;
  }
  .contact-address { margin-bottom: 8px; }
  .contact-line {
    display: flex;
    align-items: center;
    gap: 10px;
  }
  .contact-line svg { width: 14px; height: 14px; flex: none; }
</style>
</head>
<body>
<main class="stage">
  <section class="card card--front" aria-label="Card front">
    <div class="front-wordmark">QEL MOTOR GEAR INC</div>
  </section>

  <section class="card card--back" aria-label="Card back">
    <div class="person">
      <div class="person-text">
        <div class="person-name">DORIAN VALE</div>
        <div class="person-role">CEO/Founder</div>
      </div>
      <div class="person-bar"></div>
    </div>

    <div class="brand">
      <span class="brand-mark"></span>
      <span class="brand-name">QEL MOTOR GEAR INC</span>
    </div>

    <div class="contact">
      <div class="contact-address">240 W. Harbor Ave. Unit B<br>Fairview, CA, 90210</div>
      <div class="contact-line">
        <svg viewBox="0 0 16 16" aria-hidden="true"><path fill="var(--accent)" d="M3.6 1.5l2.3 2.6-1.3 1.8c.9 2 2.5 3.6 4.5 4.5l1.8-1.3 2.6 2.3-1.4 2.2C6.6 15.3.7 9.4.9 2.9z"/></svg>
        <span>1-800-555-0142</span>
      </div>
      <div class="contact-line">
        <svg viewBox="0 0 16 16" aria-hidden="true"><rect x="1" y="3" width="14" height="10" fill="var(--accent)"/><path d="M1 3l7 6 7-6" fill="none" stroke="var(--card)" stroke-width="1.4"/></svg>
        <span>sales@qelmotorgear.com</span>
      </div>
      <div class="contact-line">
        <svg viewBox="0 0 16 16" aria-hidden="true"><g fill="none" stroke="var(--accent)" stroke-width="1.4"><circle cx="8" cy="8" r="6.5"/><ellipse cx="8" cy="8" rx="2.8" ry="6.5"/><path d="M1.5 8h13"/></g></svg>
        <span>www.qelmotorgear.com</span>
      </div>
    </div>
  </section>
</main>
</body>
</html>
```